KBT Business Cards

We require business cards for our business. We would like a matte black back to the card, with our logo centred in the middle. The front side of the card is open to design.

Target Market(s)

Clients looking for legal services (professional)

Industry/Entity Type

Legal

Contact Information for Business Card

Doran Kelbrath
Partner
Mobile: 0461 738 524
Email: doran@kbtlaw.co
Website: www.kbtlaw.co
Level 3, 118 Wendmore Street
Sydney NSW 2000

Font styles to use
Other font styles liked:
• Avenir

Colors
f04a50
ffffff
1b1b1b

Requirements
Must have
• Black back with logo included in the centre of the card.
• Our font is Avenir.

```html
<!DOCTYPE html>
<html lang="en">
<head>
<meta charset="utf-8">
<title>KBT Business Cards</title>
<link rel="stylesheet" href="https://fonts.googleapis.com/css2?family=Nunito+Sans:wght@400;600;800&display=swap">
<style>
  :root {
    --brand-red: #f04a50;
    --card-red: #d2224a;
    --white: #ffffff;
    --card-black: #1b1b1b;
    --stage: #2a2a2c;
    --gloss: #4a4a4c;
    --rule: #bdbdbd;
  }
  * { box-sizing: border-box; margin: 0; padding: 0; }
  html, body {
    width: 1200px; height: 779px; overflow: hidden;
    background: var(--stage);
    font-family: "Nunito Sans", "Avenir", sans-serif;
  }
  .sheet {
    width: 1200px; height: 779px;
    display: flex; align-items: center; justify-content: center; gap: 40px;
  }
  .card {
    position: relative;
    width: 540px; height: 330px;
    background: var(--card-black);
    border-bottom: 3px solid var(--card-red);
    border-left: 2px solid var(--card-red);
    box-shadow: 0 18px 40px rgba(0,0,0,.45);
  }
  /* back */
  .card--back .mark {
    position: absolute; inset: 0;
    display: flex; align-items: center; justify-content: center; gap: 16px;
    color: var(--gloss);
  }
  .mark__square { width: 54px; height: 54px; background: var(--gloss); }
  .mark__name {
    font-weight: 800; font-size: 20px; line-height: 1.05;
    letter-spacing: .5px; text-transform: uppercase;
  }
  /* front */
  .card--front .brand {
    position: absolute; top: 46px; right: 46px;
    display: flex; align-items: center; gap: 14px;
  }
  .brand__square { width: 42px; height: 42px; background: var(--card-red); }
  .brand__name {
    color: var(--white); font-weight: 800; font-size: 17px;
    line-height: 1.05; text-transform: uppercase; letter-spacing: .3px;
  }
  .rule {
    position: absolute; left: 40px; right: 40px; top: 186px;
    height: 1px; background: var(--rule);
  }
  .person { position: absolute; left: 40px; top: 148px; }
  .person__name { color: var(--card-red); font-weight: 800; font-size: 24px; line-height: 1.1; }
  .person__role { color: var(--white); font-size: 16px; font-weight: 600; margin-top: 6px; position: relative; top: 8px; }
  .address {
    position: absolute; right: 40px; top: 198px;
    color: var(--white); font-size: 14px; line-height: 1.35; text-align: right;
  }
  .contacts {
    position: absolute; left: 40px; top: 226px;
    list-style: none; color: var(--white); font-size: 15px; line-height: 1.5;
  }
  .contacts li { display: flex; align-items: center; gap: 10px; }
  .contacts svg { width: 16px; height: 16px; fill: none; stroke: var(--card-red); stroke-width: 2; }
  .contacts svg .solid { fill: var(--card-red); stroke: none; }
</style>
</head>
<body>
<main class="sheet">
  <section class="card card--back" aria-label="Card back">
    <div class="mark">
      <span class="mark__square"></span>
      <span class="mark__name">Kelbrath<br>Brenner<br>Thorne</span>
    </div>
  </section>

  <section class="card card--front" aria-label="Card front">
    <div class="brand">
      <span class="brand__square"></span>
      <span class="brand__name">Kelbrath<br>Brenner<br>Thorne</span>
    </div>

    <div class="person">
      <h1 class="person__name">Doran Kelbrath</h1>
      <p class="person__role">Partner</p>
    </div>

    <div class="rule"></div>

    <address class="address" style="font-style:normal">
      Level 3<br>118 Wendmore Street<br>Sydney NSW 2000
    </address>

    <ul class="contacts">
      <li>
        <svg viewBox="0 0 16 16"><rect x="4" y="1.5" width="8" height="13" rx="1.5"/><circle class="solid" cx="8" cy="12" r="1"/></svg>
        0461 738 524
      </li>
      <li>
        <svg viewBox="0 0 16 16"><rect class="solid" x="1" y="4" width="14" height="9"/><path d="M1 4l7 5 7-5" stroke="#1b1b1b" stroke-width="1.4"/></svg>
        doran@kbtlaw.co
      </li>
      <li>
        <svg viewBox="0 0 16 16"><circle class="solid" cx="8" cy="8" r="7"/><path d="M4 6h3l1 3-2 2M10 3l1 3 3 1" stroke="#1b1b1b" stroke-width="1.3"/></svg>
        www.kbtlaw.co
      </li>
    </ul>
  </section>
</main>
</body>
</html>
```